Signboard menu for a Fastfood takeaway shop

My current signboard menu is old now, I want to upgrade to a new, bigger and brighter signboard menu.
Photos of the old menu attached but there are some changes in each sections of the menu needs to be changed.
Size of the signboard :
L: 1700cm
H: 1200cm

Industry/Entity Type

Fastfood Hospitality

Colors
FFC000
F8CF3A
FAE287
FDF2CF
FEFAEE

```html
<!DOCTYPE html>
<html lang="en">
<head>
<meta charset="utf-8">
<title>Takeaway Menu Board</title>
<link href="https://fonts.googleapis.com/css2?family=Lobster&family=Pathway+Gothic+One&display=swap" rel="stylesheet">
<style>
  :root{
    --board:#f6d31f;
    --ink:#2a1c0c;
    --red:#d8121f;
    --brekky:#db1114;
    --dots:#7a6420;
    --white:#ffffff;
  }
  *{box-sizing:border-box;margin:0;padding:0}
  html,body{width:1200px;height:848px;overflow:hidden;background:#ffffff}
  .canvas{position:relative;width:1200px;height:848px;background:#ffffff}
  .board{position:absolute;left:34px;top:31px;width:1112px;height:784px;background:var(--board)}
  .divider{position:absolute;width:1.5px;background:var(--red)}
  .heading{position:absolute;font-family:"Lobster",cursive;color:var(--red);font-size:25px;line-height:30px;font-weight:400;white-space:nowrap}
  .heading.two-line{line-height:25px}
  .section{position:absolute;font-family:"Pathway Gothic One","Arial Narrow",sans-serif;color:var(--ink);--row:27.5px}
  .row{display:flex;align-items:baseline;height:var(--row);line-height:var(--row);font-size:20px;letter-spacing:-0.2px;white-space:nowrap}
  .lead{flex:1;border-bottom:1px dotted var(--dots);margin:0 5px;min-width:6px}
  .lead.blank{border:0}
  .price{text-align:right}
  .extra{font-size:15px;margin-right:6px}
  .desc{font-size:15px;line-height:18px;letter-spacing:-0.2px;white-space:nowrap}
  .sub{font-size:16px}
  .pair{display:grid}
  .indent{padding-left:81px}
  .art{position:absolute;border-radius:40%}
  .brekky{position:absolute;left:590px;top:652px;width:268px;height:131px;background:var(--brekky);border-radius:12px}
  .brekky .heading{color:var(--board);left:11px;top:4px}
  .brekky .section{left:12px;top:36px;width:238px;color:var(--white);--row:27.5px}
  .brekky .row{font-size:17px}
  .brekky .lead{border-color:rgba(255,255,255,.8)}
  .brekky .big{font-size:21px}
</style>
</head>
<body>
<div class="canvas">
  <div class="board"></div>

  <div class="divider" style="left:315px;top:90px;height:692px"></div>
  <div class="divider" style="left:586px;top:90px;height:539px"></div>
  <div class="divider" style="left:857px;top:90px;height:539px"></div>

  <!-- Column 1 -->
  <h2 class="heading" style="left:57px;top:52px">Burgers</h2>
  <div class="art" role="img" aria-label="Burger illustration" style="left:182px;top:52px;width:77px;height:58px;background:linear-gradient(#e49a3a,#5a2e14 55%,#e8a444)"></div>
  <div class="section sub" style="left:61px;top:85px;line-height:20px">Beef or Chicken</div>
  <div class="section" style="left:61px;top:108px;width:241px">
    <div class="row"><span>Plain</span><span class="lead"></span><span class="price">7.00</span></div>
    <div class="row"><span>Works</span><span class="lead"></span><span class="price">10.00</span></div>
    <div class="row"><span>Cheese</span><span class="lead"></span><span class="price">8.00</span></div>
    <div class="row"><span>Mega</span><span class="lead"></span><span class="price">15.00</span></div>
    <div class="desc" style="height:21px">Works Burger with double meat, double bacon &amp; egg</div>
    <div class="row"><span>Schnitzel burgers</span><span class="lead" style="max-width:55px"></span><span style="flex:1"></span><span class="extra">extra</span><span class="price">1.50</span></div>
    <div class="row"><span>Bacon/Cheese</span><span class="lead"></span><span class="price">9.00</span></div>
    <div class="row"><span>Hawaiian</span><span class="lead"></span><span class="price">11.00</span></div>
    <div class="desc" style="height:18.5px">Works burger with Pineapple</div>
    <div class="row"><span>Bacon/Egg</span><span class="lead"></span><span class="price">9.50</span></div>
    <div class="row"><span>Mexican</span><span class="lead"></span><span class="price">8.00</span></div>
  </div>

  <h2 class="heading" style="left:61px;top:424px">Kebabs</h2>
  <div class="art" role="img" aria-label="Kebab wrap with salad illustration" style="left:151px;top:423px;width:102px;height:45px;background:linear-gradient(90deg,#d9b68a,#8a4a22 50%,#4f9a2e)"></div>
  <div class="section" style="left:61px;top:457px;width:241px">
    <div class="row"><span>Chicken</span><span class="lead"></span><span class="price">12.50</span></div>
    <div class="row"><span>Lamb</span><span class="lead"></span><span class="price">14.50</span></div>
    <div class="row"><span>Mix</span><span class="lead"></span><span class="price">14.50</span></div>
  </div>

  <h2 class="heading two-line" style="left:57px;top:575px">Bacon &amp; Egg<br>Rolls or Wraps</h2>
  <div class="art" role="img" aria-label="Bacon and egg roll illustration" style="left:227px;top:589px;width:72px;height:43px;background:linear-gradient(#e9a84a,#fff6d8 45%,#b4452c 70%,#d98a3a)"></div>
  <div class="section" style="left:61px;top:641px;width:241px">
    <div class="row"><span>Bacon/Egg</span><span class="lead"></span><span class="price">7.00</span></div>
    <div class="row"><span>Bacon/Egg/Cheese</span><span class="lead"></span><span class="price">8.20</span></div>
    <div class="row"><span>Bacon/Egg/Cheese/Onion</span><span class="lead"></span><span class="price">9.20</span></div>
    <div class="row"><span>Wraps</span><span class="lead" style="max-width:125px"></span><span style="flex:1"></span><span class="extra">extra</span><span class="price">3.00</span></div>
  </div>

  <!-- Column 2 -->
  <h2 class="heading" style="left:330px;top:52px">Gravy Rolls</h2>
  <div class="art" role="img" aria-label="Roast meat and bread roll illustration" style="left:460px;top:47px;width:106px;height:39px;background:linear-gradient(90deg,#8a2c22,#e2a0a0 50%,#e0963a)"></div>
  <div class="section" style="left:332px;top:84px;width:243px">
    <div class="row"><span>Slow cook Beef</span><span class="lead"></span><span class="price">8.50</span></div>
    <div class="row"><span>Slow cook Pork</span><span class="lead"></span><span class="price">8.00</span></div>
    <div class="row"><span>Rissole</span><span class="lead"></span><span class="price">8.00</span></div>
    <div class="row"><span>Sausage</span><span class="lead"></span><span class="price">7.00</span></div>
    <div class="row"><span>Schnitzel</span><span class="lead"></span><span class="price">8.00</span></div>
    <div class="row"><span>Chips</span><span class="lead"></span><span class="price">6.50</span></div>
  </div>

  <h2 class="heading" style="left:330px;top:256px">Schnitzel Wraps</h2>
  <div class="art" role="img" aria-label="Salad wrap illustration" style="left:498px;top:252px;width:54px;height:34px;background:linear-gradient(90deg,#4f9a2e,#e0cfa6 60%,#c9a06a)"></div>
  <div class="section" style="left:332px;top:288px;width:243px">
    <div class="row"><span>Caesar</span><span class="lead"></span><span class="price">12.00</span></div>
    <div class="row"><span>Salad and Cheese</span><span class="lead"></span><span class="price">11.00</span></div>
    <div class="row"><span>Works</span><span class="lead"></span><span class="price">14.50</span></div>
    <div class="desc" style="height:23.5px">with Bacon, Egg, Cheese and all salad</div>
    <div class="row"><span>Mexican</span><span class="lead"></span><span class="price">10.50</span></div>
    <div class="desc" style="height:46px;line-height:19px;padding-top:2px">Mexican spiced Schnitzel with Lettuce, Tomato,<br>Spanish onion, Cheese, Sour Cream and Hot chilli sauce</div>
    <div class="row"><span>Hawaiian</span><span class="lead"></span><span class="price">12.00</span></div>
    <div class="desc" style="line-height:19px;padding-top:2px">with Bacon, Lettuce, Tomato, Pineapple,<br>Cheese with Honey mustard</div>
  </div>

  <h2 class="heading" style="left:330px;top:543px">Snack Packs</h2>
  <div class="section" style="left:332px;top:577px;width:243px;--row:24.5px">
    <div class="desc" style="height:42px;line-height:18.5px">Kebab meats with Chips, Spanish Onions, Cheese<br>and Sauce of your choice</div>
    <div class="row"><span>Chicken</span><span class="lead"></span><span class="price">13.00</span></div>
    <div class="row"><span>Lamb</span><span class="lead"></span><span class="price">15.00</span></div>
    <div class="row"><span>Mix</span><span class="lead"></span><span class="price">15.00</span></div>
  </div>

  <h2 class="heading" style="left:330px;top:701px">Salad in Tubs</h2>
  <div class="section" style="left:332px;top:738px;width:243px;--row:24.5px">
    <div class="row"><span>Plain Salad</span><span class="lead"></span><span class="price">7.50</span></div>
    <div class="row"><span>Caesar Salad</span><span class="lead"></span><span class="price">10.00</span></div>
  </div>

  <!-- Column 3 -->
  <h2 class="heading" style="left:604px;top:55px">Hot Food</h2>
  <div class="art" role="img" aria-label="Sausage illustration" style="left:737px;top:53px;width:80px;height:32px;background:linear-gradient(#e8412a,#b3160f)"></div>
  <div class="section" style="left:604px;top:89px;width:236px">
    <div class="pair" style="grid-template-columns:108px 1fr;column-gap:18px">
      <div class="row"><span>Scallops</span><span class="lead"></span><span class="price">2.00</span></div>
      <div class="row"><span>Dim Sim</span><span class="lead blank"></span><span class="price">2.00</span></div>
      <div class="row"><span>Hash Brown</span><span class="lead blank"></span><span class="price">2.50</span></div>
      <div class="row"><span>Sausage</span><span class="lead blank"></span><span class="price">3.00</span></div>
      <div class="row"><span>Corn jack</span><span class="lead"></span><span class="price">2.50</span></div>
      <div class="row"><span>Chicken Stick</span><span class="lead blank"></span><span class="price">3.70</span></div>
      <div class="row"><span>Chicky Roll</span><span class="lead blank"></span><span class="price">3.50</span></div>
      <div class="row"><span>Spring Roll</span><span class="lead blank"></span><span class="price">3.50</span></div>
      <div class="row"><span>Battered Sav</span><span class="lead blank"></span><span class="price">3.50</span></div>
      <div class="row"><span>Dippa Dog</span><span class="lead blank"></span><span class="price">4.50</span></div>
    </div>
    <div class="row"><span>Mini Chicken Dim Sim x 6</span><span class="lead"></span><span class="price">3.00</span></div>
    <div class="row"><span>Chips</span><span class="lead" style="max-width:40px"></span><span style="margin-left:5px">Small</span><span class="lead"></span><span class="price">4.00</span></div>
    <div class="row indent"><span>Medium</span><span class="lead"></span><span class="price">6.00</span></div>
    <div class="row indent"><span>Large</span><span class="lead"></span><span class="price">8.00</span></div>
    <div class="row"><span>Add Gravy</span><span class="lead"></span><span class="price">2.00</span></div>
  </div>
  <div class="art" role="img" aria-label="Fries in a carton illustration" style="left:618px;top:283px;width:51px;height:50px;border-radius:6px;background:linear-gradient(#f2c43a,#e6a430 55%,#f3d8a8)"></div>

  <h2 class="heading" style="left:604px;top:386px">Sandwiches</h2>
  <div class="art" role="img" aria-label="Sandwich illustration" style="left:760px;top:378px;width:73px;height:37px;background:linear-gradient(#f1d9a8,#4f9a2e 45%,#d8362a 60%,#f1d9a8)"></div>
  <div class="section" style="left:604px;top:420px;width:236px;--row:27px">
    <div class="pair" style="grid-template-columns:108px 1fr;column-gap:33px">
      <div class="row"><span>Blackspread</span><span class="lead"></span><span class="price">4.60</span></div>
      <div class="row"><span>Cheese</span><span class="lead"></span><span class="price">4.50</span></div>
      <div class="row"><span>Tomato</span><span class="lead"></span><span class="price">4.50</span></div>
      <div class="row"><span>Salad</span><span class="lead"></span><span class="price">7.00</span></div>
      <div class="row"><span>Ham</span><span class="lead"></span><span class="price">7.50</span></div>
      <div class="row"><span>Chicken</span><span class="lead"></span><span class="price">7.50</span></div>
      <div class="row"><span>Roast Beef</span><span class="lead blank"></span><span class="price">7.50</span></div>
      <div class="row"><span>Rissole</span><span class="lead blank"></span><span class="price">7.50</span></div>
      <div class="row"><span>Sausage</span><span class="lead"></span><span class="price">7.00</span></div>
      <div class="row"><span>Scallop</span><span class="lead"></span><span class="price">6.00</span></div>
      <div class="row"><span>Chip</span><span class="lead"></span><span class="price">6.00</span></div>
      <div class="row"><span>Bacon</span><span class="lead"></span><span class="price">7.00</span></div>
      <div class="row"><span>Bacon/Egg</span><span class="lead blank"></span><span class="price">7.00</span></div>
      <div class="row"><span>Schnitzel</span><span class="lead"></span><span class="price">8.50</span></div>
      <div class="row"><span>Roll</span><span class="lead"></span><span class="price">.50¢</span></div>
    </div>
  </div>

  <div class="brekky">
    <h2 class="heading">Big Brekky Special</h2>
    <div class="art" role="img" aria-label="Takeaway coffee cup illustration" style="left:231px;top:22px;width:25px;height:37px;border-radius:4px;background:linear-gradient(#3a2a1e 15%,#ffffff 15%,#ffffff 35%,#d89a5a 35%,#d89a5a 75%,#ffffff 75%)"></div>
    <div class="section">
      <div class="row"><span>Bacon, 2x Eggs, Sausage, Fried Tomato,</span></div>
      <div class="row"><span>Hashbrown and Toast</span><span class="lead"></span><span class="price big">15.00</span></div>
      <div class="row"><span>with a small coffee</span><span class="lead"></span><span class="price big">17.00</span></div>
    </div>
  </div>

  <!-- Column 4 -->
  <h2 class="heading" style="left:875px;top:56px">Extras</h2>
  <div class="section" style="left:875px;top:89px;width:240px">
    <div class="pair" style="grid-template-columns:108px 1fr;column-gap:34px">
      <div class="row"><span>Pineapple</span><span class="lead"></span><span class="price">1.00</span></div>
      <div class="row"><span>Sauce</span><span class="lead"></span><span class="price">.50¢</span></div>
      <div class="row"><span>Avocado</span><span class="lead"></span><span class="price">1.20</span></div>
      <div class="row"><span>Cheese</span><span class="lead"></span><span class="price">1.20</span></div>
    </div>
    <div class="row"><span>Tomato/Beetroot/Onion/Cucumber</span><span class="lead blank"></span><span class="price">.50¢</span></div>
    <div class="pair" style="grid-template-columns:108px 1fr;column-gap:34px">
      <div class="row"><span>Bacon/Meat</span><span class="lead blank"></span><span class="price">2.50</span></div>
      <div class="row"><span>Egg</span><span class="lead"></span><span class="price">1.50</span></div>
    </div>
    <div class="row"><span>Kebab Meat <span class="sub">100g</span></span></div>
    <div class="pair" style="grid-template-columns:108px 1fr;column-gap:34px">
      <div class="row"><span>Chicken</span><span class="lead"></span><span class="price">3.50</span></div>
      <div class="row"><span>Lamb</span><span class="lead"></span><span class="price">4.50</span></div>
    </div>
  </div>

  <h2 class="heading" style="left:875px;top:277px">Seafood</h2>
  <div class="art" role="img" aria-label="Fried fish and chips plate illustration" style="left:991px;top:270px;width:90px;height:39px;background:linear-gradient(#e0782a,#f2c43a 60%,#7ab0dc)"></div>
  <div class="section" style="left:875px;top:309px;width:240px">
    <div class="row"><span>Calamari Ring</span><span class="lead"></span><span class="price">2.00</span></div>
    <div class="row"><span>Cocktail Fish</span><span class="lead"></span><span class="price">2.50</span></div>
    <div class="row"><span>Crab Stick</span><span class="lead"></span><span class="price">2.50</span></div>
    <div class="row"><span>Prawn Cutlet</span><span class="lead"></span><span class="price">2.50</span></div>
    <div class="row"><span>Fish Cake</span><span class="lead"></span><span class="price">3.50</span></div>
    <div class="row"><span>Battered Fish</span><span class="lead"></span><span class="price">7.00</span></div>
  </div>

  <h2 class="heading" style="left:875px;top:497px">Seafood pack</h2>
  <div class="art" role="img" aria-label="Seafood platter illustration" style="left:1039px;top:484px;width:92px;height:45px;background:linear-gradient(#d8362a,#f08a3a 55%,#3a7ac0)"></div>
  <div class="section" style="left:875px;top:529px;width:240px">
    <div class="row"><span>#1 Traditional</span><span class="lead"></span><span class="price">9.00</span></div>
    <div class="desc" style="height:24.5px">Battered Fish &amp; Chip</div>
    <div class="row"><span>#2 Snacking Pack</span><span class="lead"></span><span class="price">9.00</span></div>
    <div class="desc" style="height:18.5px">3 Cocktail Fish &amp; Chip</div>
    <div class="row"><span>#3 Fisherman Basket</span><span class="lead"></span><span class="price">18.00</span></div>
    <div class="desc" style="height:46.5px;line-height:20px">2 Calamari ring, 2 Prawn cutlet, 1 Crabstick,<br>1 Cocktail Fish, Chip &amp; 1 can of soft drink</div>
    <div class="row"><span>#4 Family Feast</span><span class="lead"></span><span class="price">40.00</span></div>
    <div class="desc" style="line-height:20px">4 Prawn cutlets, 4 Calamari rings, 4 Crabstick,<br>6 cocktail fish &amp; 1.25l bottle of soft drink</div>
  </div>
</div>
</body>
</html>
```